Dental Practice Billboard Design

We are a newer dental practice in need of a simple but appealing billboard for our growing dental practice to attract new patients. The practice is owned by husband and wife dentists and is family friendly in a small town in Kentucky. We try to be very friendly and caring to our patients. Would prefer a blue background for the billboard and our tooth logo to be prominent. We are partial to the Patua One font used in the image below but please feel free to tweak it as you deem necessary. The shape of the uppercase D and lowercase g are why we like that font, so fonts with a similarly shaped “D” and “g” would work as well. Please include our phone number (555) 847-1390. Please see our website Harlowbrookdentistry.example for more info on the practice if needed. Thank you! Looking forward to seeing your creation.
Updates

The dimensions will be 12ft x 24ft (3.6576m x 7.3152m). Apologies for not including this in the original prompt. Thank you all for your submissions.

Industry/Entity Type

Dental

Font styles to use
Other font styles liked:
• Patua One

Colors
0054AA
0677BA
7BADD7
CADEEF
E8F1F8
0094D4
00A9DD
6FCCEA
C7EBF8
E9F6FB
00AB8E
00BBA5
67D7C9
C6EFE9
E9F9F6
59FF00
82FF00
B8FF75
E3FFCB
F4FFEA

Requirements
Must have
• Phone number, website, Logo, Practice name “Harlow Brook Dentistry”
Should not have
• A tagline or slogan

```html
<!DOCTYPE html>
<html lang="en">
<head>
<meta charset="utf-8">
<title>Harlow Brook Dentistry Billboard</title>
<link rel="stylesheet" href="https://fonts.googleapis.com/css2?family=Fira+Sans:wght@600&family=Patua+One&display=swap">
<style>
  :root {
    --page: #e9f1f8;
    --board-blue: #253c85;
    --band-teal: #5ab9ad;
    --leaf-green: #6ab945;
    --white: #ffffff;
  }
  * { margin: 0; padding: 0; box-sizing: border-box; }
  html, body { width: 1200px; height: 1000px; overflow: hidden; }
  body {
    background: var(--page);
    display: flex;
    align-items: center;
    justify-content: center;
  }
  .billboard {
    position: relative;
    width: 1012px;
    height: 509px;
    background: var(--board-blue);
    overflow: hidden;
  }
  .brand-mark {
    position: absolute;
    left: 70px;
    top: 70px;
    width: 240px;
    height: 240px;
    border-radius: 50%;
    background: var(--leaf-green);
  }
  .practice-name {
    position: absolute;
    left: 345px;
    top: 56px;
    width: 650px;
    font-family: "Patua One", Georgia, serif;
    font-weight: 400;
    color: var(--white);
    text-align: center;
    line-height: 1;
  }
  .practice-name .name-main { display: block; font-size: 92px; }
  .practice-name .name-sub { display: block; font-size: 64px; margin-top: 56px; }
  .contact-line {
    position: absolute;
    left: 0;
    top: 370px;
    width: 100%;
    font-family: "Fira Sans", Arial, sans-serif;
    font-weight: 600;
    font-size: 19px;
    color: var(--white);
    text-align: center;
  }
  .call-band {
    position: absolute;
    left: 0;
    bottom: 0;
    width: 100%;
    height: 102px;
    background: var(--band-teal);
    font-family: "Fira Sans", Arial, sans-serif;
    font-weight: 600;
    font-size: 66px;
    color: var(--white);
    text-align: center;
    line-height: 102px;
    letter-spacing: 1px;
  }
</style>
</head>
<body>
  <div class="billboard">
    <div class="brand-mark" aria-hidden="true"></div>
    <h1 class="practice-name">
      <span class="name-main">Harlow Brook</span>
      <span class="name-sub">Dentistry</span>
    </h1>
    <p class="contact-line">Harlowbrookdentistry@example.com | Harlowbrookdentistry.example</p>
    <p class="call-band">CALL TODAY! (555) 847-1390</p>
  </div>
</body>
</html>
```